Buch-/E-Book-Cover für Referenzbuch der Industrie
Zielgruppe
Als Manufaktur einzigartiger Fachmedien präsentiert verlag-technova Schlüsseltechnologien und ihre Märkte. Faszination für Technik ist die Grundlage unserer Arbeit. Mehr als 30 Jahre verlegerische Erfahrung und das Verständnis für Technologiemärkte machen uns zu einem anerkannten Partner der Industrie.
Unsere Medienmarken knüpfen ein starkes und weit verzweigtes Netzwerk – Print und digital – , in dem sich Anbieter und Anwender von Technologien und Produkten in ihren Zielsetzungen wiederfinden.
Unsere Magazine, Events und Netzwerkveranstaltungen sowie kundenspezifische Kommunikations- & Strategiekampagnen setzen in ihren Zielmärkten Maßstäbe und genießen bei Lesern, Kunden und Partnern Vertrauen und Respekt.
Für das ausgeschriebene Projekt handelt es sich um unsere Referenzpublikation MACHINA.ahead LUMEVETA.
LUMEVETA {polynesisch: Freiraum}
Das Referenzbuch der Industrie. Für Vorwärtsdenker und Zukunftsmacher.
Wandel bestimmt unsere Zeit und verändert unsere Gesellschaft, unsere Unternehmen, uns alle.
Im Wandel liegt Freiraum zur Gestaltung. Gesellschaftlicher Wandel, Technologie-Wandel, Klimawandel, Wertewandel, Führungswandel oder Organisationswandel sind nur einige Beispiele. Wer dabei den Wandel in engen Bahnen denkt, verschenkt Potential. Veränderung braucht Freiraum für neue Ideen und Perspektiven sowie Persönlichkeiten, die diesen nutzen wollen.
Aber wer gestaltet die Zukunft der Industrie und ihrer Branchen? Und wie?
Wir geben Personen aus der Industrie den Freiraum, ihre Perspektiven auf und aus dem Wandel zu erzählen. Warum? Weil sie uns begeistert haben, in persönlichen Treffen und Gesprächen, durch streitbare Meinungen und ehrliche Geschichten. Weil sie die Zukunft verändern.
LUMEVETA ist eine Aufforderung: Zum Mitdenken, Weiterdenken, aber auch Nachdenken.
LUMEVETA – RAUM FÜR NEUES
Ein Referenzbuch, d..
Aufgabenstellung
1. Kurzzusammenfassung der Ausschreibung
Die 4. Ausgabe des jährlichen Referenzbuchs der Industrie, MACHINA.ahead LUMEVETA 2025, erscheint im Oktober 2024. Für das Cover sucht der verlag-technova Verlag neue Vorschläge, die die Themen Freiraum und Wandel in den Fokus stellen.
2. Gestalterische & Inhaltliche Anforderungen
• Format: 195x250 mm + Anschnitt
• Rücken: ca. 1,6 cm (Stand letzte Publikation 2023)
• Auflösung: Druckqualität, mind. 300 dpi
• Inhaltliche Elemente:
- LUMEVETA Schriftzug
- {polynesisch: Freiraum}
- Untersatz: Das Referenzbuch der Industrie. Für Vorwärtsdenker und Zukunftsmacher.
- part of MACHINA.ahead Logo-Balken am unteren Rand (siehe Beispiel AuD_Titelbeispiel_Logobalken)
WICHTIG: Der aktuelle Schriftzug LUMEVETA und die Farbe Orange (0/80/100/0) (siehe Beispiel LUMEVETA 2021) sollen als Wiedererkennung in die Gestaltungen eingebunden werden.

```html
<!DOCTYPE html>
<html lang="de">
<head>
<meta charset="utf-8">
<title>MACHINA.ahead LUMEVETA 2024 – Cover</title>
<link rel="stylesheet" href="https://fonts.googleapis.com/css2?family=Bebas+Neue&family=Oswald:wght@300;400;500&family=Roboto+Condensed:wght@700&display=swap">
<style>
  :root {
    --brand-orange: #e8510f;
    --paper: #ffffff;
    --backdrop: #4b4b4b;
    --ink: #1a1a1a;
    --logo-part: #8c1430;
    --logo-name: #b3105c;
  }
  * { margin: 0; padding: 0; box-sizing: border-box; }
  html, body {
    width: 1200px; height: 1200px; overflow: hidden;
    background: var(--backdrop);
  }
  .cover {
    position: absolute; left: 132px; top: 0;
    width: 936px; height: 1200px;
    background: var(--paper);
    overflow: hidden;
  }
  .wordmark-row {
    position: absolute; left: 0; width: 318px; height: 276px;
    display: block;
  }
  .wordmark-row text {
    font-family: "Bebas Neue", "Oswald", sans-serif;
    fill: var(--brand-orange);
  }
  .row-1 { top: 0; }
  .row-2 { top: 295px; }
  .row-3 { top: 629px; }
  .row-4 { top: 924px; }
  .translation {
    position: absolute; left: 76px; top: 592px;
    width: 168px; text-align: center;
    font-family: "Roboto Condensed", "Arial Narrow", sans-serif;
    font-weight: 700; font-size: 13.5px; color: var(--ink);
    white-space: nowrap;
  }
  .hero-art {
    position: absolute; left: 0; top: 0;
    width: 936px; height: 1200px;
  }
  .edition-year {
    position: absolute; right: 61px; top: 700px;
    font-family: "Oswald", sans-serif; font-weight: 500;
    font-size: 88px; line-height: 1; color: var(--brand-orange);
    letter-spacing: 1px;
  }
  .tagline {
    position: absolute; right: 61px; top: 808px;
    text-align: right;
    font-family: "Oswald", sans-serif; font-weight: 300;
    font-size: 31px; line-height: 42px; color: var(--ink);
    letter-spacing: -0.5px;
  }
  .logo-bar {
    position: absolute; right: 61px; top: 1103px;
    display: flex; align-items: baseline; gap: 18px;
    font-family: "Oswald", sans-serif;
  }
  .logo-bar .part-of {
    font-weight: 400; font-size: 26px; color: var(--logo-part);
  }
  .logo-bar .network-name {
    font-weight: 500; font-size: 52px; line-height: 1;
    color: var(--logo-name);
  }
</style>
</head>
<body>
  <main class="cover">
    <svg class="hero-art" viewBox="0 0 936 1200" role="img" aria-label="Photograph of colourful origami figures stacked in a rising sequence: a crumpled paper ball, a paper boat, a swan and a bird taking flight">
      <defs>
        <linearGradient id="origami-tones" x1="0" y1="0" x2="0" y2="1">
          <stop offset="0" stop-color="#e0261c"/>
          <stop offset="0.3" stop-color="#d56fd6"/>
          <stop offset="0.48" stop-color="#8a4fd0"/>
          <stop offset="0.62" stop-color="#1f86e6"/>
          <stop offset="0.76" stop-color="#16d0de"/>
          <stop offset="0.86" stop-color="#27b537"/>
          <stop offset="1" stop-color="#f4a21d"/>
        </linearGradient>
      </defs>
      <path d="M340 60 H880 V700 H600 V1000 H340 Z" fill="url(#origami-tones)" opacity="0.22"/>
    </svg>

    <svg class="wordmark-row row-1" viewBox="0 0 318 276" aria-hidden="true"><text x="0" y="276" font-size="394" textLength="318" lengthAdjust="spacingAndGlyphs">LU</text></svg>
    <svg class="wordmark-row row-2" viewBox="0 0 318 276" aria-hidden="true"><text x="0" y="276" font-size="394" textLength="318" lengthAdjust="spacingAndGlyphs">ME</text></svg>
    <p class="translation">{polynesisch – Freiraum}</p>
    <svg class="wordmark-row row-3" viewBox="0 0 318 276" aria-hidden="true"><text x="0" y="276" font-size="394" textLength="318" lengthAdjust="spacingAndGlyphs">VE</text></svg>
    <svg class="wordmark-row row-4" viewBox="0 0 318 276" aria-hidden="true"><text x="0" y="276" font-size="394" textLength="318" lengthAdjust="spacingAndGlyphs">TA</text></svg>
    <h1 style="position:absolute;width:1px;height:1px;overflow:hidden;clip:rect(0 0 0 0)">LUMEVETA</h1>

    <p class="edition-year">2024</p>
    <p class="tagline">Das Referenzbuch<br>der Industrie.<br>Für Vorwärtsdenker<br>und Zukunftsmacher.</p>

    <div class="logo-bar">
      <span class="part-of">part of</span>
      <span class="network-name">MACHINA.ahead</span>
    </div>
  </main>
</body>
</html>
```